E learning Platform for privacy

Current website is as below and its more of a shell.
I need someone to take the text and content and design it properly.
https://study.vornaquill.com/

After that, design has to be implemented with elementor and wordpress
https://elementor.com/

```html
<!DOCTYPE html>
<html lang="en">
<head>
<meta charset="utf-8">
<title>Vornaquill Learning Centre</title>
<link href="https://fonts.googleapis.com/css2?family=Montserrat:ital,wght@0,400;0,500;0,600;0,700;0,800;1,400&display=swap" rel="stylesheet">
<style>
:root{
  --orange:#f7941d;
  --orange-deep:#ef5f24;
  --grey:#58595b;
  --grey-dark:#3f3f41;
  --grey-mid:#8a8a8c;
  --grey-light:#f4f4f4;
  --footer:#6b6b6d;
  --white:#fff;
}
*{box-sizing:border-box;margin:0;padding:0}
html,body{width:1200px;height:3674px;overflow:hidden}
body{position:relative;font-family:'Montserrat',sans-serif;color:var(--grey);background:var(--white)}
.abs{position:absolute}
a{color:inherit;text-decoration:none}

/* header */
.top-line{left:0;top:0;width:1200px;height:3px;background:var(--orange)}
.brand{left:143px;top:52px;display:flex;align-items:center;gap:10px;font-weight:700;font-size:30px;color:var(--orange-deep);letter-spacing:1px}
.brand-dot{width:22px;height:22px;border-radius:50%;background:var(--grey)}
.phone{left:592px;top:18px;display:flex;align-items:center;gap:10px;font-size:21px;font-weight:600;color:var(--grey)}
.phone-ico{width:36px;height:36px;border:2px solid var(--orange-deep);border-radius:50%;display:flex;align-items:center;justify-content:center}
.socials{left:862px;top:24px;display:flex;gap:6px}
.socials span{width:28px;height:28px;border-radius:50%;background:var(--grey-mid)}
.nav{left:400px;top:79px;font-size:14px;font-weight:500;color:var(--grey)}
.nav a{position:absolute;white-space:nowrap}
.nav .active::after{content:"";position:absolute;left:0;right:0;top:26px;height:3px;background:var(--orange);box-shadow:0 -5px 0 -1px var(--orange)}
.btn-pill{height:36px;border-radius:18px;display:flex;align-items:center;justify-content:center;font-size:13px;font-weight:700;color:var(--white)}
.signin{left:849px;top:70px;width:99px;background:var(--orange)}
.register{left:955px;top:70px;width:101px;background:var(--grey)}

/* hero */
.hero{left:0;top:120px;width:1200px;height:572px;overflow:hidden}
.hero-photo{position:absolute;inset:0;background:linear-gradient(90deg,#ededed 0%,#e7e4e1 40%,#d6cdc4 60%,#c9b7a6 75%,#d9d6d2 100%)}
.hero-curve{position:absolute;left:0;top:0}
.hero h1{position:absolute;left:141px;top:118px;font-size:60px;line-height:70px;font-weight:800;letter-spacing:.5px}
.hero h1 .o{color:var(--orange-deep)}
.hero h1 .g{color:var(--grey)}
.hero p{position:absolute;left:142px;top:285px;font-size:20px;line-height:29px;font-weight:600;color:var(--grey)}
.hero .cta{position:absolute;left:144px;top:384px;width:182px;height:57px;border-radius:29px;background:var(--orange);color:var(--white);font-size:14px;font-weight:700;display:flex;align-items:center;justify-content:center;gap:8px}
.dots{position:absolute;left:572px;top:514px;display:flex;gap:4px}
.dots span{width:8px;height:8px;border-radius:50%;background:var(--white)}
.dots .on{background:var(--orange)}

/* headings */
.sec-title{left:0;width:1200px;text-align:center;font-size:33px;font-weight:800;color:var(--grey-dark)}
.sec-title .o{color:var(--orange-deep)}
.rule{left:561px;width:78px;height:8px;border-top:3px solid var(--orange);border-bottom:3px solid var(--orange)}

/* features */
.roadmap-art{left:392px;top:920px;width:421px;height:329px;border-radius:50px;background:linear-gradient(135deg,#f7941d 0%,#c9bdb0 50%,#6d6e70 100%)}
.feature h3{font-size:15px;font-weight:500;line-height:20px;color:var(--grey-dark)}
.feature p{font-size:11.5px;line-height:20px;color:var(--grey-mid);margin-top:12px}
.feature .more{display:block;font-size:11.5px;font-weight:700;color:var(--orange-deep);margin-top:13px}
.feature.left{text-align:right;width:260px}
.feature.right{width:250px}
.outline-btn{left:509px;width:182px;height:56px;border:2px solid var(--grey);border-radius:28px;display:flex;align-items:center;justify-content:center;gap:8px;font-size:16px;font-weight:500;color:var(--orange)}

/* courses */
.courses-bg{left:0;top:1477px;width:1200px;height:749px;background:var(--grey-light);border-radius:0 150px 0 150px}
.card{width:402px;height:168px;background:var(--white);border:1px solid #dcdcdc}
.card .thumb{position:absolute;left:6px;top:6px;width:183px;height:156px;display:flex;align-items:center;justify-content:center}
.play{width:52px;height:52px;border-radius:50%;border:3px solid var(--white);display:flex;align-items:center;justify-content:center}
.card h4{position:absolute;left:212px;top:14px;width:135px;font-size:16px;line-height:19px;font-weight:700;color:var(--grey-dark)}
.card .cat{position:absolute;left:212px;top:62px;font-size:11px;color:var(--grey)}
.card .cat b{font-weight:400;color:var(--orange)}
.card .meta{position:absolute;left:212px;top:90px;font-size:11px;color:var(--grey);display:flex;align-items:center;gap:5px}
.card .meta i{width:9px;height:9px;border-radius:50%;border:2px solid var(--orange);display:inline-block}
.card .enroll{position:absolute;left:212px;top:125px;width:77px;height:27px;border-radius:14px;background:var(--orange);color:var(--white);font-size:10px;font-weight:700;display:flex;align-items:center;justify-content:center}
.free{position:absolute;right:-1px;top:-1px;width:62px;height:21px;background:var(--orange);color:var(--white);font-size:11px;font-weight:700;display:flex;align-items:center;justify-content:center;clip-path:polygon(12% 0,100% 0,100% 100%,0 100%)}

/* blog */
.post{width:444px;height:400px}
.post .img{position:absolute;left:0;top:0;width:444px;height:295px}
.post .cap{position:absolute;left:30px;top:248px;width:400px;height:60px;background:var(--white);border-radius:50px 0 0 0}
.post h4{position:absolute;left:67px;top:282px;font-size:20px;font-weight:600;color:var(--grey-dark)}
.post .meta{position:absolute;left:67px;top:318px;font-size:11.5px;color:var(--grey)}
.post .meta b{font-weight:400;color:var(--orange)}
.post .read{position:absolute;left:69px;top:352px;width:131px;height:37px;border-radius:19px;background:var(--orange);color:var(--white);font-size:13px;font-weight:700;display:flex;align-items:center;justify-content:center}

/* testimonial */
.say-bg{left:0;top:2933px;width:1200px;height:470px}
.say-title{color:var(--grey-dark)}
.say-title .w{color:var(--white)}
.rule.white{border-color:var(--white)}
.avatar{left:161px;top:3148px;width:126px;height:126px;border-radius:50%;background:linear-gradient(135deg,#d9b8a0,#8e5a3e)}
.quote-mark{left:203px;top:3259px;width:37px;height:37px;border-radius:50%;background:var(--grey);color:var(--white);font-size:22px;font-weight:800;font-style:italic;display:flex;align-items:center;justify-content:center}
.say-text{left:334px;top:3155px;width:730px;font-size:13.5px;line-height:28.5px;font-style:italic;color:var(--white)}
.say-name{left:334px;top:3258px;font-size:18px;font-weight:700;color:var(--white);display:flex;align-items:center;gap:22px}

/* footer */
.footer{left:0;top:3403px;width:1200px;height:271px;background:var(--footer)}
.f-social{left:535px;top:3448px;display:flex;gap:7px}
.f-social span{width:28px;height:28px;border-radius:50%;background:var(--white);opacity:.85}
.f-links{left:0;top:3502px;width:1200px;text-align:center;font-size:15px;font-weight:700;color:var(--white);letter-spacing:.3px}
.f-links span{margin:0 12px}
.copy{left:0;top:3541px;width:1200px;text-align:center;font-size:11px;color:var(--white)}
.partners{left:490px;top:3592px;display:flex;align-items:center;gap:28px;color:var(--white)}
.partners .p1{font-size:26px;font-weight:600}
.partners .p2{font-size:9px;line-height:11px}
.partners .p2 b{display:block;font-size:22px;font-weight:600;line-height:26px}
</style>
</head>
<body>

<div class="abs top-line"></div>

<header>
  <div class="abs brand"><span class="brand-dot"></span>VORNAQUILL</div>
  <div class="abs phone">
    <span class="phone-ico"><svg width="18" height="18" viewBox="0 0 24 24"><path d="M6.6 10.8a15 15 0 0 0 6.6 6.6l2.2-2.2c.3-.3.7-.4 1-.2 1.1.4 2.3.6 3.6.6.6 0 1 .4 1 1V20c0 .6-.4 1-1 1A17 17 0 0 1 3 4c0-.6.4-1 1-1h3.5c.6 0 1 .4 1 1 0 1.3.2 2.5.6 3.6.1.3 0 .7-.2 1z" fill="#ef5f24"/></svg></span>
    +1 (800) 555 01 48
  </div>
  <div class="abs socials" aria-label="Social links"><span></span><span></span><span></span><span></span><span></span><span></span></div>
  <nav class="abs nav">
    <a class="active" style="left:0">HOME</a>
    <a style="left:70px">BLOGS</a>
    <a style="left:142px">COURSES</a>
    <a style="left:234px">CONTACT US</a>
    <a style="left:349px">ABOUT US</a>
  </nav>
  <a class="abs btn-pill signin">SIGN IN</a>
  <a class="abs btn-pill register">REGISTER</a>
</header>

<section class="abs hero">
  <div class="hero-photo" role="img" aria-label="Photo of a smiling student using a tablet in a library"></div>
  <svg class="hero-curve" width="1200" height="572" viewBox="0 0 1200 572">
    <path d="M0 0 H560 C520 180 520 420 470 572 H160 C70 560 0 500 0 430 Z" fill="#efefef" opacity=".9"/>
    <path d="M0 430 C0 510 70 565 160 572 H0 Z" fill="#f7941d"/>
    <path d="M0 412 C8 500 80 560 160 562 L150 572 C70 565 0 510 0 430 Z" fill="#ffffff"/>
  </svg>
  <h1><span class="o">DATA PROTECTION</span><br><span class="g">EXCELLENCE</span></h1>
  <p>Largest online e-learning resource for data<br>Protection &amp; privacy</p>
  <a class="cta">GET TRAINED <svg width="13" height="13" viewBox="0 0 14 14"><circle cx="7" cy="7" r="7" fill="#fff"/><path d="M5 4l3.5 3L5 10" stroke="#f7941d" stroke-width="2" fill="none"/></svg></a>
  <div class="dots"><span></span><span></span><span class="on"></span><span></span><span></span></div>
</section>

<!-- why section -->
<h2 class="abs sec-title" style="top:782px">WHY THE (VORNAQUILL) <span class="o">LEARNING</span> CENTRE?</h2>
<div class="abs rule" style="top:838px"></div>

<div class="abs roadmap-art" role="img" aria-label="Illustration of a winding learning roadmap with four milestone icons"></div>

<div class="abs feature left" style="left:111px;top:933px">
  <h3>COMPREHENSIVE<br>ROADMAP</h3>
  <p>Our objective is to provide a<br>comprehensive competency roadmap,<br>instead of one-off courses.</p>
  <a class="more">READ MORE</a>
</div>
<div class="abs feature right" style="left:829px;top:933px">
  <h3>ACADEMIC &amp; INTERNATIONAL<br>CERTIFICATION</h3>
  <p>We partner with prominent universities<br>in the region as well as international<br>certification bodies.</p>
  <a class="more">READ MORE</a>
</div>
<div class="abs feature left" style="left:111px;top:1132px">
  <h3>OPERATIONAL<br>PERSPECTIVE</h3>
  <p>We cover a broad range of data protection<br>topics from both a legal and operational<br>perspective, covering multiple</p>
  <a class="more">READ MORE</a>
</div>
<div class="abs feature right" style="left:829px;top:1132px">
  <h3>MODULAR APPROACH<br>&amp; FLEXIBILITY</h3>
  <p>All our courses are modular in nature to<br>cater to the busy professional, meaning<br>that you can take the courses.</p>
  <a class="more">READ MORE</a>
</div>

<a class="abs outline-btn" style="top:1321px">LEARN MORE <svg width="14" height="14" viewBox="0 0 14 14"><circle cx="7" cy="7" r="7" fill="#f7941d"/><path d="M5 4l3.5 3L5 10" stroke="#fff" stroke-width="2" fill="none"/></svg></a>

<!-- courses -->
<div class="abs courses-bg"></div>
<h2 class="abs sec-title" style="top:1560px">FEATURED <span class="o">COURSES</span></h2>
<div class="abs rule" style="top:1617px"></div>

<article class="abs card" style="left:185px;top:1681px">
  <div class="thumb" role="img" aria-label="Course video preview" style="background:linear-gradient(135deg,#3e7fc4,#2f62a8)"><span class="play"><svg width="18" height="20"><path d="M3 1l14 9-14 9z" fill="#fff"/></svg></span></div>
  <span class="free">FREE</span>
  <h4>How to Scale Social Impact</h4>
  <div class="cat">Category : <b>General</b></div>
  <div class="meta"><i></i>55 Weeks &nbsp;|&nbsp; <i style="border-radius:2px"></i>Mr.Example</div>
  <a class="enroll">ENROLL</a>
</article>
<article class="abs card" style="left:614px;top:1681px">
  <div class="thumb" role="img" aria-label="Course video preview" style="background:linear-gradient(135deg,#bfc1c0,#5c615e)"><span class="play"><svg width="18" height="20"><path d="M3 1l14 9-14 9z" fill="#fff"/></svg></span></div>
  <h4 style="width:175px">Quillbase Demo Course</h4>
  <div class="cat">Category : <b>General</b></div>
  <div class="meta"><i></i>55 Weeks &nbsp;|&nbsp; <i style="border-radius:2px"></i>Mr.Example</div>
  <a class="enroll">ENROLL</a>
</article>
<article class="abs card" style="left:185px;top:1868px">
  <div class="thumb" role="img" aria-label="Course video preview" style="background:linear-gradient(135deg,#e8e8e6,#5a5a58)"><span class="play"><svg width="18" height="20"><path d="M3 1l14 9-14 9z" fill="#fff"/></svg></span></div>
  <h4 style="width:175px">Nemo enim ipsam voluptatem</h4>
  <div class="cat">Category : <b>General</b></div>
  <div class="meta"><i></i>55 Weeks &nbsp;|&nbsp; <i style="border-radius:2px"></i>Mr.Example</div>
  <a class="enroll">ENROLL</a>
</article>
<article class="abs card" style="left:614px;top:1868px">
  <div class="thumb" role="img" aria-label="Course video preview" style="background:linear-gradient(135deg,#e9e9e9,#3a3a3a)"><span class="play"><svg width="18" height="20"><path d="M3 1l14 9-14 9z" fill="#fff"/></svg></span></div>
  <span class="free">FREE</span>
  <h4>Sed ut perspic iatis unde</h4>
  <div class="cat">Category : <b>General</b></div>
  <div class="meta"><i></i>55 Weeks &nbsp;|&nbsp; <i style="border-radius:2px"></i>Mr.Example</div>
  <a class="enroll">ENROLL</a>
</article>

<a class="abs outline-btn" style="top:2083px">VIEW MORE <svg width="14" height="14" viewBox="0 0 14 14"><circle cx="7" cy="7" r="7" fill="#f7941d"/><path d="M5 4l3.5 3L5 10" stroke="#fff" stroke-width="2" fill="none"/></svg></a>

<!-- blog -->
<h2 class="abs sec-title" style="top:2316px">BLOG <span class="o">POSTS</span></h2>
<div class="abs rule" style="top:2372px"></div>

<article class="abs post" style="left:144px;top:2452px">
  <div class="img" role="img" aria-label="Photo of a person writing notes beside a laptop" style="background:linear-gradient(135deg,#b59a62,#3c4a55)"></div>
  <div class="cap"></div>
  <h4>How to write blog</h4>
  <div class="meta">Last Updated December 18, 2019 Posted by <b>coursevane_admin</b></div>
  <a class="read">READ MORE</a>
</article>
<article class="abs post" style="left:624px;top:2452px">
  <div class="img" role="img" aria-label="Photo of a stack of books turning into a digital screen" style="background:linear-gradient(135deg,#2f3336,#3d6c99 70%,#1b1d20)"></div>
  <div class="cap"></div>
  <h4>Hello world!</h4>
  <div class="meta">Last Updated December 18, 2019 Posted by <b>coursevane_admin</b></div>
  <a class="read">READ MORE</a>
</article>

<!-- testimonial -->
<div class="abs footer"></div>
<svg class="abs say-bg" width="1200" height="470" viewBox="0 0 1200 470" role="img" aria-label="Orange-toned photo of a student studying">
  <defs><linearGradient id="sayGrad" x1="0" y1="0" x2="1" y2="1"><stop offset="0" stop-color="#f07a3c"/><stop offset="1" stop-color="#e8622b"/></linearGradient></defs>
  <path d="M120 0 H1200 V330 C1200 400 1150 460 1060 470 H0 V120 C0 50 50 0 120 0 Z" fill="url(#sayGrad)"/>
  <path d="M1200 330 C1200 410 1150 458 1060 466" stroke="#fff" stroke-width="4" fill="none"/>
</svg>
<h2 class="abs sec-title say-title" style="top:3025px">WHAT <span class="w">PEOPLE SAY</span></h2>
<div class="abs rule white" style="top:3083px"></div>
<div class="abs avatar" role="img" aria-label="Portrait of the reviewer"></div>
<div class="abs quote-mark">&#8220;</div>
<p class="abs say-text">Lorem ipsum dolor sit amet, consectetur adipiscing elit, sed do eiusmod tempor incididunt ut labore et dolore magna aliqua. Ut enim ad minim veniam, quis nostrud exercitatioea commodo consuis aute irure dolor in reprehenderit in voluptate velit esse cillum dolore eu fugiat nulla pariatur.</p>
<div class="abs say-name">- JOHN DOE
  <svg width="82" height="16" viewBox="0 0 82 16"><g fill="none" stroke="#fff" stroke-width="1.2"><path id="st" d="M8 1l2 5h5l-4 3 1.6 5L8 11l-4.6 3L5 9 1 6h5z"/><use href="#st" x="16.5"/><use href="#st" x="33"/><use href="#st" x="49.5"/><use href="#st" x="66"/></g></svg>
</div>

<!-- footer -->
<div class="abs f-social" aria-label="Social links"><span></span><span></span><span></span><span></span></div>
<nav class="abs f-links">ABOUT<span>/</span>COURSES<span>/</span>FAQS<span>/</span>GET INVOLVED<span>/</span>BLOG<span>/</span>CONTACT</nav>
<p class="abs copy">© Vornaquill Centre 2020 - All rights reserved &nbsp;|&nbsp; Privacy policy</p>
<div class="abs partners">
  <span class="p1">Coursevane</span>
  <span class="p2">POWERED BY<b>Open Lattice</b></span>
</div>

</body>
</html>
```